U.S. Popcorn company needs business cards

We are a popcorn company that manufactures popcorn and sells it to grocery stores worldwide. Our theme is "Americana" and our logo is U.S. route 66 which is the most famous highway in the U.S.

We would like the design to be simple and to use both sides. On the back side we would like to see just the logo and website. The front would be normal details

Target Market(s)

Wholesalers, grocers and distributors

Industry/Entity Type

Manufacture

Contact Information for Business Card

Business name: Prairie Lantern Popcorn
Phone: +1 555 308 4726
Email: Dale@prairielanternpopcorn.com
website: www.prairielanternpopcorn.com
Tag Line: "Fresh from the kettle"
Name: Dale Whitcombe
Title: Founder/President

Requirements
Must have
• Either this design should be fun or clean and simple. I will let you show me your thougths.
Nice to have
• Anything that ties in the real Hwy Route 66.
• Colors might need to be red, white and blue incorporated.
Should not have
• Not be too busy.

```html
<!DOCTYPE html>
<html lang="en">
<head>
<meta charset="utf-8">
<title>Prairie Lantern Popcorn – Business Card</title>
<link rel="stylesheet" href="https://fonts.googleapis.com/css2?family=Lato:wght@400;700&display=swap">
<style>
  :root {
    --page-bg: #e9e6e1;
    --navy: #0d1742;
    --navy-deep: #060b26;
    --navy-light: #1d2a66;
    --red: #c4171f;
    --red-dark: #8f0d13;
    --tan: #cbbf9f;
    --silver: #d9d6d0;
    --white: #f4f4f6;
    --frost-top: #f3f5f8;
    --frost-mid: #dfe7f1;
    --frost-low: #efe3e6;
  }
  * { margin: 0; padding: 0; box-sizing: border-box; }
  html, body {
    width: 1200px; height: 970px; overflow: hidden;
    background: var(--page-bg);
    font-family: "Lato", Arial, sans-serif;
  }
  .card {
    position: absolute; left: 80px; top: 189px;
    width: 1040px; height: 592px;
    overflow: hidden;
    box-shadow: 0 14px 40px rgba(0,0,0,0.25);
  }
  .card-shape { position: absolute; inset: 0; }
  .brand-mark {
    position: absolute; left: 40px; top: 250px; width: 390px;
    display: flex; align-items: center; justify-content: center; gap: 14px;
  }
  .brand-dot {
    width: 30px; height: 30px; border-radius: 50%;
    background: var(--navy); flex: none;
  }
  .brand-name {
    font-size: 32px; font-weight: 700; color: var(--navy); line-height: 1.15;
  }
  .details { position: absolute; left: 560px; top: 70px; color: var(--silver); }
  .company { font-size: 40px; font-weight: 400; color: var(--tan); letter-spacing: 0.3px; }
  .company .accent { color: var(--white); }
  .tagline { font-size: 26px; margin-top: 8px; color: var(--tan); }
  .person { margin-top: 40px; }
  .person-name { font-size: 36px; color: var(--silver); line-height: 1; }
  .person-title { font-size: 26px; color: var(--red); line-height: 1.1; margin-top: 2px; }
  .address { margin-top: 44px; font-size: 26px; line-height: 35px; padding-left: 4px; letter-spacing: 0.3px; }
  .contacts { list-style: none; margin-top: 36px; font-size: 26px; color: var(--tan); }
  .contacts li { display: flex; align-items: center; height: 34px; }
  .contacts svg { width: 26px; height: 22px; margin-right: 20px; flex: none; fill: var(--red); }
</style>
</head>
<body>
  <div class="card">
    <svg class="card-shape" viewBox="0 0 1040 592" width="1040" height="592" aria-hidden="true">
      <defs>
        <linearGradient id="frost" x1="0" y1="0" x2="0" y2="1">
          <stop offset="0" stop-color="var(--frost-top)"/>
          <stop offset="0.55" stop-color="var(--frost-mid)"/>
          <stop offset="1" stop-color="var(--frost-low)"/>
        </linearGradient>
        <linearGradient id="navyPanel" x1="0" y1="0" x2="1" y2="1">
          <stop offset="0" stop-color="var(--navy-light)"/>
          <stop offset="0.5" stop-color="var(--navy)"/>
          <stop offset="1" stop-color="var(--navy-deep)"/>
        </linearGradient>
      </defs>
      <rect width="1040" height="592" fill="url(#frost)"/>
      <path d="M497 0 C470 80 470 180 490 280 C510 380 500 500 452 592 L1040 592 L1040 0 Z" fill="var(--red-dark)"/>
      <path d="M505 0 C482 80 482 180 502 280 C522 380 512 500 470 592 L1040 592 L1040 0 Z" fill="var(--red)"/>
      <path d="M512 0 C490 80 492 180 512 280 C532 380 524 500 502 592 L1040 592 L1040 0 Z" fill="var(--silver)"/>
      <path d="M517 0 C496 80 498 180 518 280 C538 380 530 500 510 592 L1040 592 L1040 0 Z" fill="url(#navyPanel)"/>
    </svg>

    <div class="brand-mark">
      <span class="brand-dot"></span>
      <span class="brand-name">Prairie Lantern Popcorn</span>
    </div>

    <div class="details">
      <h1 class="company">Prairie Lantern <span class="accent">Popcorn</span></h1>
      <p class="tagline">Fresh from the kettle</p>

      <div class="person">
        <p class="person-name">Dale Whitcombe</p>
        <p class="person-title">Founder/President</p>
      </div>

      <p class="address">Harlow Springs, KS<br>United States</p>

      <ul class="contacts">
        <li>
          <svg viewBox="0 0 26 22"><path d="M2 7 C2 3 24 3 24 7 L24 9 L18 9 L18 6 L8 6 L8 9 L2 9 Z M7 10 L19 10 L23 20 L3 20 Z"/></svg>
          +1 555 308 4726
        </li>
        <li>
          <svg viewBox="0 0 26 22"><path d="M2 4 L24 4 L24 19 L2 19 Z M4 6 L13 13 L22 6 Z" fill-rule="evenodd"/></svg>
          Dale@prairielanternpopcorn.com
        </li>
        <li>
          <svg viewBox="0 0 26 22"><circle cx="13" cy="11" r="10"/><path d="M3 11 H23 M13 1 C8 6 8 16 13 21 M13 1 C18 6 18 16 13 21" stroke="var(--navy)" stroke-width="1.4" fill="none"/></svg>
          www.prairielanternpopcorn.com
        </li>
      </ul>
    </div>
  </div>
</body>
</html>
```